Global (re)insurance broker needs a business card design

We need a classic business card for our company that is headquartered in SG, with offices in Malaysia and Dubai. We specialise in insurance and reinsurance broking and consultancy for our global clients.

```html
<!DOCTYPE html>
<html lang="en">
<head>
<meta charset="utf-8">
<title>Meridane Business Card</title>
<link rel="stylesheet" href="https://fonts.googleapis.com/css2?family=Open+Sans:wght@400;600;700;800&display=swap">
<style>
  :root {
    --backdrop: #232323;
    --card-dark: #1f1f24;
    --brand-blue: #2a4aa6;
    --brand-blue-deep: #22408f;
    --brand-blue-light: #3556b8;
    --brand-mint: #c5e0b4;
    --text-light: #ffffff;
    --rule: #8a8a90;
  }
  * { box-sizing: border-box; margin: 0; padding: 0; }
  html, body {
    width: 1200px;
    height: 780px;
    overflow: hidden;
    background: var(--backdrop);
    font-family: "Open Sans", Arial, sans-serif;
  }
  .canvas {
    width: 1200px;
    height: 780px;
    display: flex;
    align-items: center;
    justify-content: center;
    gap: 60px;
  }
  .card {
    position: relative;
    width: 525px;
    height: 300px;
    overflow: hidden;
    box-shadow: 0 10px 24px rgba(0,0,0,0.55);
  }

  /* Reverse side */
  .card-reverse {
    background: var(--brand-blue);
  }
  .reverse-texture {
    position: absolute;
    inset: 0;
    background:
      linear-gradient(160deg, var(--brand-blue-light) 0%, var(--brand-blue) 45%, var(--brand-blue-deep) 100%);
  }
  .reverse-wordmark {
    position: absolute;
    left: 0; right: 0;
    top: 50%;
    transform: translateY(-50%);
    text-align: center;
    color: var(--text-light);
    font-weight: 700;
    font-size: 58px;
    letter-spacing: 2px;
  }

  /* Front side */
  .card-front {
    background: var(--card-dark);
  }
  .front-wordmark {
    position: absolute;
    top: 52px;
    left: 150px;
    color: var(--brand-mint);
    font-weight: 700;
    font-size: 56px;
    letter-spacing: 2px;
  }
  .person {
    position: absolute;
    left: 100px;
    top: 160px;
  }
  .person-name {
    font-weight: 800;
    font-size: 30px;
    line-height: 1.05;
  }
  .person-name .given { color: var(--brand-blue-light); }
  .person-name .family { color: var(--brand-mint); }
  .person-title {
    color: var(--text-light);
    font-weight: 600;
    font-size: 13px;
    margin-top: 2px;
  }
  .divider {
    position: absolute;
    left: 300px;
    top: 148px;
    width: 1px;
    height: 80px;
    background: var(--rule);
  }
  .contact-list {
    position: absolute;
    left: 318px;
    top: 152px;
    list-style: none;
  }
  .contact-list li {
    display: flex;
    align-items: center;
    gap: 9px;
    color: var(--text-light);
    font-size: 12.5px;
    height: 24px;
  }
  .contact-list svg { width: 13px; height: 13px; flex: none; }
  .address-band {
    position: absolute;
    left: 0;
    right: 0;
    bottom: 30px;
    height: 26px;
    background: var(--brand-blue);
    color: var(--text-light);
    font-size: 13px;
    font-weight: 600;
    line-height: 26px;
    text-align: center;
    letter-spacing: 0.3px;
  }
</style>
</head>
<body>
<main class="canvas">

  <section class="card card-reverse" aria-label="Card reverse">
    <div class="reverse-texture" role="img" aria-label="Repeating company name pattern in tonal blue"></div>
    <div class="reverse-wordmark">MERIDANE</div>
  </section>

  <section class="card card-front" aria-label="Card front">
    <div class="front-wordmark">MERIDANE</div>

    <div class="person">
      <div class="person-name"><span class="given">Mira</span> <span class="family">Lowen</span></div>
      <div class="person-title">Chief Operating Officer</div>
    </div>

    <div class="divider"></div>

    <ul class="contact-list">
      <li>
        <svg viewBox="0 0 16 16" aria-hidden="true"><rect x="4" y="1" width="8" height="14" rx="1.5" fill="none" stroke="#ffffff" stroke-width="1.4"/><line x1="7" y1="12.5" x2="9" y2="12.5" stroke="#ffffff" stroke-width="1.2"/></svg>
        +65 5550 0142
      </li>
      <li>
        <svg viewBox="0 0 16 16" aria-hidden="true"><circle cx="8" cy="8" r="7" fill="#3556b8"/><ellipse cx="8" cy="8" rx="3" ry="7" fill="none" stroke="#1f1f24" stroke-width="1"/><line x1="1" y1="8" x2="15" y2="8" stroke="#1f1f24" stroke-width="1"/></svg>
        www.meridane.com
      </li>
      <li>
        <svg viewBox="0 0 16 16" aria-hidden="true"><rect x="1" y="4" width="14" height="10" fill="none" stroke="#c5e0b4" stroke-width="1.4"/><polyline points="1,4 8,10 15,4" fill="none" stroke="#c5e0b4" stroke-width="1.4"/></svg>
        mira@meridane.com
      </li>
    </ul>

    <div class="address-band">22 Harbour Lane, Quay Tower #08-04, Singapore 049321</div>
  </section>

</main>
</body>
</html>
```